Business Card Design

Business Card for professional consulting firm working with large financial institutions.

Target Market(s)

Executive buyers

Industry/Entity Type

Banking

Contact Information for Business Card

Mild creativity wanted. Not boring, but do elaborate artwork.

Font styles to use
Serif
Sans Serif

Colors

Designer to choose colors to be used in the design.

Requirements
Must have
• Standard business card features - company name, individual name, telephone, website, email, locations.
Nice to have
• Two colors
Should not have
• too many colors, fancy printing, cartoons.

```html
<!DOCTYPE html>
<html lang="en">
<head>
<meta charset="utf-8">
<title>Northvale — Business Card</title>
<link rel="stylesheet" href="https://fonts.googleapis.com/css2?family=Oswald:wght@600&family=Work+Sans:wght@400&display=swap">
<style>
  :root {
    --stage: #2f2f2f;
    --card-white: #ffffff;
    --card-white-shade: #ececec;
    --name-grey: #a9a9a9;
    --ink: #2b2b2b;
    --icon-grey: #8a8a8a;
    --back-light: #b9b9b9;
    --back-dark: #8e8e8e;
    --back-mark: #d9d9d9;
  }
  * { box-sizing: border-box; margin: 0; padding: 0; }
  html, body { width: 1200px; height: 900px; overflow: hidden; }
  body {
    background: var(--stage);
    display: flex;
    flex-direction: column;
    align-items: center;
    justify-content: center;
    gap: 40px;
    font-family: "Work Sans", Arial, sans-serif;
  }
  .card {
    width: 700px;
    height: 400px;
    border-radius: 24px;
    position: relative;
    overflow: hidden;
  }
  .card-front {
    background: radial-gradient(ellipse at 70% 40%, var(--card-white) 40%, var(--card-white-shade) 100%);
    color: var(--ink);
  }
  .identity {
    position: absolute;
    left: 110px;
    top: 120px;
    width: 250px;
    text-align: right;
  }
  .person-name {
    font-family: "Oswald", "Arial Narrow", sans-serif;
    font-weight: 600;
    font-size: 44px;
    letter-spacing: 0.5px;
    line-height: 1;
    color: var(--name-grey);
    text-transform: uppercase;
  }
  .person-role {
    font-size: 17px;
    margin-top: 4px;
  }
  .divider {
    position: absolute;
    left: 385px;
    top: 170px;
    width: 2px;
    height: 66px;
    background: var(--ink);
  }
  .contact-list {
    position: absolute;
    left: 410px;
    top: 172px;
    list-style: none;
    font-size: 18px;
    line-height: 22px;
  }
  .contact-list li { display: flex; align-items: center; gap: 10px; }
  .contact-list svg { width: 12px; height: 12px; flex: none; }
  .address {
    position: absolute;
    left: 70px;
    top: 300px;
    font-size: 17px;
  }
  .card-back {
    background: linear-gradient(160deg, var(--back-light), var(--back-dark));
    display: flex;
    align-items: center;
    justify-content: center;
  }
  .company-name {
    font-size: 76px;
    font-weight: 400;
    color: var(--back-mark);
    letter-spacing: 1px;
  }
</style>
</head>
<body>
  <section class="card card-front" aria-label="Business card front">
    <div class="identity">
      <h1 class="person-name">Daniel Hart</h1>
      <p class="person-role">Director</p>
    </div>
    <div class="divider"></div>
    <ul class="contact-list">
      <li>
        <svg viewBox="0 0 12 12" aria-hidden="true"><path d="M3 1 L5 3.5 L4 5 Q5 7 7 8 L8.5 7 L11 9 L9.5 11 Q4 10.5 1 2.5 Z" fill="none" stroke="var(--icon-grey)" stroke-width="1"/></svg>
        +330 2460-5172
      </li>
      <li>
        <svg viewBox="0 0 12 12" aria-hidden="true"><rect x="1" y="2.5" width="10" height="7" fill="none" stroke="var(--icon-grey)" stroke-width="1"/><path d="M1 2.5 L6 6.5 L11 2.5" fill="none" stroke="var(--icon-grey)" stroke-width="1"/></svg>
        info@northvale.com
      </li>
      <li>
        <svg viewBox="0 0 12 12" aria-hidden="true"><circle cx="6" cy="6" r="5" fill="var(--icon-grey)"/><path d="M1 6 H11 M6 1 V11" stroke="var(--card-white)" stroke-width="0.8"/></svg>
        www.northvale.com
      </li>
    </ul>
    <p class="address">48 Harlow St, Kingsbury VIC 3712</p>
  </section>

  <section class="card card-back" aria-label="Business card back">
    <p class="company-name">Northvale</p>
  </section>
</body>
</html>
```